Professional & attention grabbing.

A business card design, front and back. I already have a logo I will attach, but I am open to something new as well.
Things to include:
Name:
Title:
Phone:
Email:
Wanting something that is professional but attention grabbing.
Also we do a lot of work using drones on natural gas pipelines (leading the future)if you want to include any of that. I'm open to ideas.
Target Market(s)
Natural gas transmission industry / greenhouse gas mitigation industry
Industry/Entity Type
Business
Colors
Designer to choose colors to be used in the design.
Look and feel
Each slider illustrates characteristics of the customer's brand and the style your logo design should communicate.

```html
<!DOCTYPE html>
<html lang="en">
<head>
<meta charset="utf-8">
<title>Kestrel Inspections – Business Card</title>
<link rel="stylesheet" href="https://fonts.googleapis.com/css2?family=Open+Sans:wght@400;600;700&display=swap">
<style>
  :root {
    --backdrop: #e6e2dc;
    --card-white: #ffffff;
    --card-black: #1f1f1f;
    --brand-red: #c1272d;
    --ink: #1d1d1d;
    --ink-soft: #2a2a2a;
  }
  * { margin: 0; padding: 0; box-sizing: border-box; }
  html, body {
    width: 1200px; height: 1000px; overflow: hidden;
    background: var(--backdrop);
    font-family: "Open Sans", Arial, sans-serif;
  }
  .canvas { position: relative; width: 1200px; height: 1000px; }

  .card {
    position: absolute; left: 266px; width: 666px; height: 397px;
    overflow: hidden;
    box-shadow: 0 6px 14px rgba(0,0,0,0.25);
  }
  .card--front { top: 74px; background: var(--card-white); }
  .card--back { top: 533px; background: var(--card-black); }

  .front-band {
    position: absolute; top: 0; right: 0; width: 232px; height: 100%;
    background: var(--card-black);
  }

  .brand { position: absolute; display: flex; align-items: center; gap: 12px; }
  .brand__mark { width: 26px; height: 26px; background: var(--brand-red); flex: none; }
  .brand__name { font-weight: 700; letter-spacing: 0.5px; white-space: nowrap; }
  .card--front .brand { left: 32px; top: 48px; }
  .card--front .brand__name { font-size: 30px; color: var(--ink); }
  .card--back .brand { left: 50%; top: 50%; transform: translate(-50%, -50%); gap: 16px; }
  .card--back .brand__mark { width: 36px; height: 36px; }
  .card--back .brand__name { font-size: 40px; color: #ffffff; }

  .person { position: absolute; left: 33px; top: 186px; }
  .person__name { font-size: 20px; font-weight: 600; color: var(--brand-red); letter-spacing: 0.3px; line-height: 1.2; }
  .person__title { font-size: 15px; color: var(--ink-soft); margin-top: 2px; }

  .address { position: absolute; left: 33px; top: 252px; font-size: 15px; line-height: 20px; color: var(--ink-soft); }

  .contacts { position: absolute; left: 33px; top: 302px; list-style: none; }
  .contacts li { display: flex; align-items: center; gap: 8px; font-size: 15px; line-height: 23.5px; color: var(--ink-soft); }
  .contacts svg { width: 14px; height: 14px; fill: var(--brand-red); flex: none; }
</style>
</head>
<body>
<div class="canvas">

  <section class="card card--front" aria-label="Business card front">
    <div class="front-band"></div>

    <div class="brand">
      <span class="brand__mark"></span>
      <span class="brand__name">KESTREL INSPECTIONS</span>
    </div>

    <div class="person">
      <p class="person__name">DARO VELTMAN</p>
      <p class="person__title">Managing Director</p>
    </div>

    <p class="address">4120 North Calder Lane<br>Brookfield, MD 21900</p>

    <ul class="contacts">
      <li>
        <svg viewBox="0 0 16 16" aria-hidden="true"><path d="M1 5c0-2 2-3 7-3s7 1 7 3v1h-4V4.5H5V6H1zM3 7h10l2 7H1z M8 9a2 2 0 1 0 0 4a2 2 0 1 0 0-4z"/></svg>
        + 000 000 0000
      </li>
      <li>
        <svg viewBox="0 0 16 16" aria-hidden="true"><path d="M1 3h14v10H1z M1 3l7 6l7-6" fill="var(--brand-red)"/><path d="M1.5 3.5l6.5 5.5l6.5-5.5" fill="none" stroke="#fff" stroke-width="1.3"/></svg>
        info@kestrelinspect.com
      </li>
      <li>
        <svg viewBox="0 0 16 16" aria-hidden="true"><circle cx="8" cy="8" r="7"/><path d="M3 8h10M8 1.5c-3 3-3 10 0 13M8 1.5c3 3 3 10 0 13" fill="none" stroke="#fff" stroke-width="1.1"/></svg>
        www.kestrelinspect.com
      </li>
    </ul>
  </section>

  <section class="card card--back" aria-label="Business card back">
    <div class="brand">
      <span class="brand__mark"></span>
      <span class="brand__name">KESTREL INSPECTIONS</span>
    </div>
  </section>

</div>
</body>
</html>
```